Vantoq Business Card Project showing the logo and a marbo image on the rear

Design a whacky but professional business card, the logo is for the front and the Marbo image is for the rear. Happy to consider other open source Marbo Images if the designer wants to select one from the web. Vantoq is a competitor to OMB.com.au and Pellory.com.au and is based around every property in Australia

Target Market(s)

Business

Contact Information for Business Card

Name, Title, Email, Web, Phone Number

Font styles to use
Other font styles liked:
• avenir

Requirements
Must have
• Image on Back logo on front
Nice to have
• Happy to consider other images on rear, preftably Colin Marbo. Image supplied I own, we can use open source other Marbo Images

```html
<!DOCTYPE html>
<html lang="en">
<head>
<meta charset="utf-8">
<title>Vantoq Business Card</title>
<link href="https://fonts.googleapis.com/css2?family=Nunito+Sans:wght@400;700;800&display=swap" rel="stylesheet">
<style>
  :root {
    --backdrop: #2a2a2a;
    --card-white: #ffffff;
    --card-black: #1c1c1c;
    --brand-orange: #f28c1e;
    --ink: #111111;
    --text-light: #f2f2f2;
    --art-sky: #3a7fd0;
    --art-mid: #e8672a;
    --art-low: #f0c21e;
  }
  * { margin: 0; padding: 0; box-sizing: border-box; }
  html, body { width: 1200px; height: 988px; overflow: hidden; }
  body {
    background: var(--backdrop);
    font-family: "Nunito Sans", "Avenir", sans-serif;
    position: relative;
  }
  .card {
    position: absolute;
    left: 220px;
    width: 760px;
    height: 434px;
    border-radius: 26px;
    overflow: hidden;
  }
  .card--back { top: 40px; }
  .card--front { top: 514px; background: var(--card-white); }

  .back-artwork {
    position: absolute; inset: 0;
    background: linear-gradient(170deg, var(--art-sky) 0%, #2c5fb0 30%, #6a4a8c 48%, var(--art-mid) 66%, #d63a3a 80%, var(--art-low) 100%);
  }
  .back-logo {
    position: absolute;
    left: 190px; top: 175px;
    display: flex; align-items: center; gap: 22px;
  }
  .logo-square {
    width: 70px; height: 70px;
    background: var(--brand-orange);
  }
  .back-logo .logo-name {
    font-weight: 800; font-size: 96px; line-height: 1;
    color: var(--card-white);
    letter-spacing: 1px;
  }

  .front-wave { position: absolute; inset: 0; }
  .front-logo {
    position: absolute;
    right: 60px; top: 52px;
    display: flex; align-items: center; gap: 20px;
  }
  .front-logo .logo-square { width: 58px; height: 58px; }
  .front-logo .logo-name {
    font-weight: 800; font-size: 80px; line-height: 1;
    color: var(--ink);
  }

  .contact-block {
    position: absolute;
    left: 58px; top: 246px;
    color: var(--text-light);
  }
  .person-name {
    font-weight: 800; font-size: 24px; letter-spacing: 1px;
    color: var(--brand-orange); text-transform: uppercase; line-height: 1.1;
  }
  .person-title { font-size: 16px; margin-top: 2px; }
  .address { font-size: 15px; line-height: 20px; margin-top: 10px; }
  .contact-list { list-style: none; margin-top: 6px; }
  .contact-list li {
    display: flex; align-items: center; gap: 10px;
    font-size: 15px; line-height: 22px;
  }
  .contact-icon { width: 18px; height: 18px; flex: none; }
</style>
</head>
<body>

  <section class="card card--back" aria-label="Card back">
    <div class="back-artwork" role="img" aria-label="Colourful cartoon cityscape of buildings with faces under a blue sky with clouds, stars and sun"></div>
    <div class="back-logo">
      <span class="logo-square"></span>
      <span class="logo-name">Vantoq</span>
    </div>
  </section>

  <section class="card card--front" aria-label="Card front">
    <svg class="front-wave" viewBox="0 0 760 434" width="760" height="434" aria-hidden="true">
      <path fill="var(--card-black)" d="M0,434 L0,225 C120,160 260,215 420,215 C560,215 680,190 760,100 L760,434 Z"/>
      <path fill="var(--brand-orange)" d="M180,210 C300,212 560,222 760,70 L760,100 C680,190 560,215 420,215 C320,215 240,214 180,210 Z"/>
    </svg>

    <div class="front-logo">
      <span class="logo-square"></span>
      <span class="logo-name">Vantoq</span>
    </div>

    <div class="contact-block">
      <p class="person-name">Elias Drummond</p>
      <p class="person-title">Executive Producer</p>
      <p class="address">418 Kestrel Lane<br>Harwell County 5231</p>
      <ul class="contact-list">
        <li>
          <svg class="contact-icon" viewBox="0 0 18 18" aria-hidden="true"><circle cx="9" cy="9" r="9" fill="var(--brand-orange)"/><path d="M6 4.5c.6 0 1.3 1.6 1.3 2 0 .5-.8.8-.7 1.3.3 1 1.1 1.8 2 2.2.5.2.8-.7 1.3-.7.4 0 2 .7 2 1.3 0 .8-1 1.4-1.8 1.4C7.3 12 5 9.2 5 6.2c0-.8.4-1.7 1-1.7z" fill="#fff"/></svg>
          323-555-0148
        </li>
        <li>
          <svg class="contact-icon" viewBox="0 0 18 18" aria-hidden="true"><circle cx="9" cy="9" r="9" fill="var(--brand-orange)"/><rect x="4.5" y="6" width="9" height="6.5" fill="#fff"/><path d="M4.5 6l4.5 3.6L13.5 6" fill="none" stroke="var(--brand-orange)" stroke-width="1"/></svg>
          elias@vantoq.com.au
        </li>
        <li>
          <svg class="contact-icon" viewBox="0 0 18 18" aria-hidden="true"><circle cx="9" cy="9" r="9" fill="var(--brand-orange)"/><circle cx="9" cy="9" r="4.5" fill="none" stroke="#fff" stroke-width="1.2"/><path d="M4.5 9h9M9 4.5c-2 2.5-2 6.5 0 9M9 4.5c2 2.5 2 6.5 0 9" fill="none" stroke="#fff" stroke-width="1"/></svg>
          www.vantoq.com.au
        </li>
      </ul>
    </div>
  </section>

</body>
</html>
```